Logistics Website Design

See website https://tqfreightglobal.com for theme and color details. Need the site to be re-done and reflect some of the designs shown in this list here: https://pixelvane.com/tags/logistics-company-website

Target Market(s)

Logistics & Transportation

Industry/Entity Type

Logistics and Supply Chain

Coding

Number of Pages Required

5+ page

Requirements
Must have
• Colors must match theme of logo. Looking for a sleek, interactive design.

```html
<!DOCTYPE html>
<html lang="en">
<head>
<meta charset="utf-8">
<title>TQ Freight — Delivering Strength in Every Mile</title>
<link rel="stylesheet" href="https://fonts.googleapis.com/css2?family=Bebas+Neue&family=Oswald:wght@400;500;600&family=Inter:wght@400;500;600&display=swap">
<style>
:root{
  --bg:#140806;
  --bg-2:#1d0d09;
  --card:#2a130d;
  --card-2:#3a1a10;
  --line:#3d2219;
  --orange:#e8622e;
  --orange-2:#f07a3f;
  --peach:#f3a57f;
  --cream:#f6e6dc;
  --muted:#c9b2a6;
  --white:#ffffff;
}
*{margin:0;padding:0;box-sizing:border-box}
html,body{width:1200px;height:4264px;overflow:hidden;background:var(--bg)}
body{font-family:"Inter",sans-serif;color:var(--cream);position:relative}
.page{position:relative;width:1200px;height:4264px;overflow:hidden}
.abs{position:absolute}
.display{font-family:"Bebas Neue",sans-serif;letter-spacing:.5px;line-height:1}
.eyebrow{font-family:"Oswald",sans-serif;font-weight:500;font-size:15px;letter-spacing:4px;color:var(--cream)}
.accent{color:var(--peach)}
.btn{position:absolute;display:flex;align-items:center;gap:12px;background:var(--orange);color:var(--white);border-radius:30px;font-family:"Oswald",sans-serif;font-weight:500;font-size:15px;text-transform:uppercase;padding:0 6px 0 24px;height:44px;white-space:nowrap}
.btn .arrow{width:32px;height:32px;border-radius:50%;background:#2a130d;display:flex;align-items:center;justify-content:center;flex:none}
.photo{position:absolute}

/* nav */
.brand{position:absolute;left:82px;top:32px;display:flex;align-items:center;gap:10px}
.brand .dot{width:18px;height:18px;border-radius:50%;background:var(--orange)}
.brand span{font-family:"Oswald",sans-serif;font-weight:600;font-size:22px;color:var(--white)}
.nav{position:absolute;top:62px;left:300px;display:flex;gap:46px;font-family:"Oswald",sans-serif;font-size:14px;font-weight:500;color:var(--white)}
.nav a{display:flex;align-items:center;gap:6px;text-decoration:none;color:inherit}

/* stats */
.stat{position:absolute;top:710px;display:flex;align-items:center;gap:14px}
.stat .num{font-family:"Oswald",sans-serif;font-size:52px;font-weight:400;color:var(--cream)}
.stat .lbl{font-family:"Oswald",sans-serif;font-size:14px;color:var(--peach);line-height:1.45}

/* services */
.svc{position:absolute;top:1542px;width:256px;height:341px;border-radius:6px;overflow:hidden;background:linear-gradient(180deg,#3b1a10 0%,#241009 55%);}
.svc h3{position:absolute;left:36px;top:36px;font-family:"Oswald",sans-serif;font-weight:500;font-size:22px;line-height:1.15;color:var(--peach)}
.svc p{position:absolute;left:36px;top:98px;width:196px;font-size:11px;line-height:1.6;color:var(--cream)}
.svc .photo{left:0;right:0;bottom:0;height:140px}
.svc.active{background:var(--orange)}
.svc.active h3{color:var(--white)}
.svc.active p{color:#ffe1d2}

/* industries */
.ind{position:absolute;width:339px;height:164px;border:1px solid #4a2b20;border-radius:6px;background:linear-gradient(160deg,#1f0c08,#170806)}
.ind.active{background:linear-gradient(160deg,#3a1a10,#1d0c08);border-color:#6a3a28}
.ind .ico{position:absolute;left:28px;top:30px;width:58px;height:58px;border-radius:8px;background:var(--orange);display:flex;align-items:center;justify-content:center}
.ind h4{position:absolute;left:102px;top:30px;font-family:"Oswald",sans-serif;font-weight:500;font-size:20px;color:var(--peach)}
.ind p{position:absolute;left:102px;top:68px;width:215px;font-size:11px;line-height:1.55;color:var(--cream)}

/* testimonials */
.tcard{position:absolute;top:2805px;width:323px;height:265px;border-radius:6px;background:linear-gradient(180deg,#4a200f 0%,#2a120b 100%)}
.tcard.active{background:linear-gradient(180deg,#7a3415 0%,#3a1a10 100%)}
.tcard p{position:absolute;left:38px;top:38px;width:252px;font-size:12.5px;line-height:1.52;color:var(--cream)}
.tcard .who{position:absolute;left:42px;top:190px;font-size:15px;font-weight:600;color:var(--white)}
.tcard .stars{position:absolute;left:40px;top:212px;color:var(--cream);font-size:14px;letter-spacing:3px}
.tcard .src{position:absolute;right:38px;bottom:40px;width:20px;height:20px;border-radius:50%;background:#e9dcd2}

/* footer */
.fnav{position:absolute;left:364px;top:3825px;width:229px}
.fnav a{display:flex;align-items:center;gap:22px;height:52px;border-bottom:1px solid var(--line);padding-left:18px;font-family:"Oswald",sans-serif;font-size:22px;font-weight:500;color:var(--white);text-decoration:none}
.fnav a:last-child{border-bottom:none}
.fsvc{position:absolute;left:637px;top:3826px}
.fsvc h5,.fcontact h5{font-family:"Oswald",sans-serif;font-size:22px;font-weight:500;color:var(--white)}
.fsvc li{list-style:none;font-family:"Oswald",sans-serif;font-weight:400;font-size:19px;color:var(--peach);margin-top:10px;padding-left:26px}
.fsvc li::before{content:"» ";color:var(--peach)}
.fcontact{position:absolute;left:877px;top:3826px}
.field{width:238px;height:34px;border:1px solid #6a4a3e;border-radius:3px;margin-top:12px;display:flex;align-items:center;gap:8px;padding-left:12px;font-size:11.5px;color:var(--cream)}
.social{position:absolute;top:3986px;width:34px;height:34px;border-radius:50%;background:var(--orange)}
</style>
</head>
<body>
<div class="page">

<!-- HERO -->
<div class="photo" role="img" aria-label="White semi truck driving on a highway at sunset" style="left:26px;top:20px;width:1156px;height:658px;border-radius:8px;background:linear-gradient(100deg,#2a1108 0%,#4a2212 40%,#7a4a34 62%,#c9b7b0 78%,#6a4a3c 100%)"></div>
<div class="abs" style="left:26px;top:20px;width:1156px;height:658px;border-radius:8px;background:linear-gradient(90deg,rgba(28,10,6,.85) 0%,rgba(28,10,6,.35) 55%,rgba(28,10,6,0) 100%)"></div>

<div class="brand"><div class="dot"></div><span>TQ FREIGHT</span></div>
<nav class="nav">
  <a href="#"><svg width="12" height="12" viewBox="0 0 12 12"><path d="M6 1 1 6h2v5h2.5V8h1v3H9V6h2z" fill="#fff"/></svg>HOME</a>
  <a href="#"><svg width="13" height="13" viewBox="0 0 13 13"><path d="M2 2l9 9M11 2 2 11" stroke="#fff" stroke-width="2"/></svg>SERVICES</a>
  <a href="#"><svg width="13" height="12" viewBox="0 0 13 12"><path d="M1 11V4l3 2V4l3 2V1h2v10z" fill="#fff"/></svg>INDUSTRIES</a>
  <a href="#"><svg width="12" height="13" viewBox="0 0 12 13"><circle cx="6" cy="4" r="3" fill="none" stroke="#fff" stroke-width="1.4"/><path d="M1 12c0-3 2.5-4.5 5-4.5s5 1.5 5 4.5" fill="none" stroke="#fff" stroke-width="1.4"/></svg>ABOUT US</a>
  <a href="#"><svg width="13" height="13" viewBox="0 0 13 13"><path d="M3 1l2 3-1.5 1.5c1 2 2 3 4 4L9 8l3 2-1.5 2.5C6 12 1 7 .8 2.5z" fill="#fff"/></svg>CONTACT US</a>
</nav>
<div class="btn" style="left:946px;top:50px;height:40px;font-size:14px;padding-left:26px">REQUEST A QUOTE<span class="arrow" style="width:30px;height:30px"><svg width="12" height="12" viewBox="0 0 12 12"><path d="M2 10 10 2M4 2h6v6" stroke="#fff" stroke-width="1.6" fill="none"/></svg></span></div>

<h1 class="abs display" style="left:114px;top:232px;font-size:70px;font-weight:400">
  <span style="color:var(--peach)">DELIVERING STRENGTH</span><br><span style="color:var(--white)">IN EVERY MILE</span>
</h1>
<p class="abs" style="left:115px;top:378px;width:500px;font-size:17px;line-height:1.38;color:var(--cream)">We deliver a comprehensive range of open-deck and specialized transportation services—including flatbed, step deck, heavy haul, and over-dimensional freight solutions.</p>
<div class="btn" style="left:108px;top:478px">REQUEST A QUOTE<span class="arrow"><svg width="12" height="12" viewBox="0 0 12 12"><path d="M2 10 10 2M4 2h6v6" stroke="#fff" stroke-width="1.6" fill="none"/></svg></span></div>
<div class="btn" style="left:306px;top:478px;padding:0 28px 0 6px;flex-direction:row-reverse">CALL US NOW<span class="arrow"><svg width="14" height="14" viewBox="0 0 13 13"><path d="M3 1l2 3-1.5 1.5c1 2 2 3 4 4L9 8l3 2-1.5 2.5C6 12 1 7 .8 2.5z" fill="#fff"/></svg></span></div>

<!-- STATS -->
<div class="stat" style="left:92px"><span class="num">250</span><span class="lbl">LOREM IPSUM DOLOR SIT<br>AMET CONSECTETUR</span></div>
<div class="stat" style="left:470px"><span class="num">1500+</span><span class="lbl">LOREM IPSUM DOLOR SIT<br>AMET CONSECTETUR</span></div>
<div class="stat" style="left:882px"><span class="num">180</span><span class="lbl">LOREM IPSUM DOLOR SIT<br>AMET CONSECTETUR</span></div>
<div class="abs" style="left:55px;top:798px;width:1090px;height:1px;background:var(--line)"></div>

<!-- ABOUT -->
<div class="abs" style="left:100px;top:881px;width:456px;height:456px;border-radius:50%;border:3px solid #b0623c"></div>
<div class="photo" role="img" aria-label="Row of parked semi trucks in a sepia tone" style="left:114px;top:895px;width:428px;height:428px;border-radius:50%;background:radial-gradient(circle at 45% 45%,#d9c2b6 0%,#a78676 45%,#5a3a2e 100%)"></div>
<div class="abs eyebrow" style="left:604px;top:896px;color:var(--peach)">ABOUT COMPANY</div>
<h2 class="abs display" style="left:607px;top:924px;font-size:56px;color:var(--white)">KEEPING YOUR SUPPLY</h2>
<div class="abs display" style="left:610px;top:990px;height:58px;padding:4px 14px 0;background:var(--orange);border-radius:4px;font-size:54px;color:#2a110a">CHAIN MOVING</div>
<p class="abs" style="left:615px;top:1071px;width:500px;font-size:17px;line-height:1.45;color:var(--cream)">We deliver a comprehensive range of open-deck and specialized transportation services—including flatbed, step deck, heavy haul, and over-dimensional freight solutions. Backed by years of experience, a trusted nationwide carrier network, and a strong safety-first culture, we provide reliable, adaptable logistics support built around the unique requirements of every load.</p>
<div class="btn" style="left:615px;top:1248px;height:42px">LEARN MORE<span class="arrow"><svg width="12" height="12" viewBox="0 0 12 12"><path d="M2 10 10 2M4 2h6v6" stroke="#fff" stroke-width="1.6" fill="none"/></svg></span></div>

<div class="abs" style="left:591px;top:1305px;width:1px;height:75px;background:var(--orange)"></div>
<div class="abs" style="left:587px;top:1378px;width:8px;height:8px;border-radius:50%;background:var(--orange)"></div>

<!-- SERVICES -->
<div class="abs eyebrow" style="left:0;width:1200px;text-align:center;top:1415px">WHAT WE DO</div>
<h2 class="abs display" style="left:0;width:1200px;text-align:center;top:1440px;font-size:56px"><span class="accent">OUR</span> <span style="color:var(--white)">SERVICES</span></h2>

<div class="svc" style="left:74px">
  <h3>FLATBED<br>TRANSPORTATION</h3>
  <p>From routine shipments to oversized and heavy-haul loads, we handle freight requiring proper securement, regulatory knowledge, and consistent on-time execution.</p>
  <div class="photo" role="img" aria-label="White box truck on a road" style="background:linear-gradient(180deg,#5c4a44,#8a7a74 60%,#3b2b25)"></div>
</div>
<div class="svc active" style="left:344px">
  <h3>STEP DECK<br>TRANSPORTATION</h3>
  <p>Our step deck trucking services support tall, heavy, and specialized freight that requires additional height clearance and flexible loading options.</p>
  <div class="btn" style="left:34px;top:170px;height:30px;font-size:10px;background:#2a130d;padding-left:20px;gap:8px">LEARN MORE<span class="arrow" style="width:22px;height:22px;background:var(--orange)"><svg width="9" height="9" viewBox="0 0 12 12"><path d="M2 10 10 2M4 2h6v6" stroke="#fff" stroke-width="2" fill="none"/></svg></span></div>
  <div class="photo" role="img" aria-label="Red step deck trailer" style="background:linear-gradient(180deg,#f08a5a,#e8e2de 55%,#c23a2a)"></div>
</div>
<div class="svc" style="left:611px">
  <h3>STEP DECK<br>TRANSPORTATION</h3>
  <p>From consumer goods to industrial materials, our dry van services provide the space, security, and consistency you need coast to coast.</p>
  <div class="photo" role="img" aria-label="Dry van truck on a highway at dusk" style="background:linear-gradient(180deg,#3a3a2a,#6a5a3a 50%,#2a2a20)"></div>
</div>
<div class="svc" style="left:877px">
  <h3>HEAVY HAUL<br>TRANSPORTATION</h3>
  <p>We provide heavy haul trucking solutions for oversized, overweight, and over-dimensional freight.</p>
  <div class="photo" role="img" aria-label="Red heavy haul truck carrying a yellow excavator" style="background:linear-gradient(180deg,#7a6a64,#b8a8a0 45%,#8a3028 80%,#3a2a24)"></div>
</div>

<div class="abs" style="left:599px;top:1920px;width:1px;height:80px;background:var(--orange)"></div>
<div class="abs" style="left:595px;top:1998px;width:8px;height:8px;border-radius:50%;background:var(--orange)"></div>

<!-- INDUSTRIES -->
<div class="abs eyebrow" style="left:0;width:1200px;text-align:center;top:2038px">WHO WE SERVE</div>
<h2 class="abs display" style="left:0;width:1200px;text-align:center;top:2066px;font-size:56px"><span class="accent">INDUSTRIES</span> <span style="color:var(--white)">WE SERVE</span></h2>

<div class="ind" style="left:83px;top:2173px"><div class="ico"><svg width="30" height="30" viewBox="0 0 30 30"><rect x="5" y="13" width="20" height="13" rx="1" fill="#fff"/><circle cx="10" cy="8" r="3" fill="#fff"/><circle cx="18" cy="7" r="4" fill="#fff"/></svg></div><h4>FOOD &amp; BEVERAGE</h4><p>TQ Freight provides reliable, compliant, and efficient trucking solutions for the food and beverage industry.</p></div>
<div class="ind active" style="left:442px;top:2173px"><div class="ico"><svg width="30" height="30" viewBox="0 0 30 30"><path d="M3 6h4l3 13h13l3-9H9" fill="none" stroke="#fff" stroke-width="2.4"/><circle cx="12" cy="24" r="2.2" fill="#fff"/><circle cx="21" cy="24" r="2.2" fill="#fff"/></svg></div><h4 style="top:36px">E-COMMERCE &amp; RETAIL</h4><p style="top:74px">TQ Freight provides reliable, compliant, and efficient trucking solutions for the food and beverage industry.</p></div>
<div class="ind" style="left:799px;top:2173px"><div class="ico"><svg width="30" height="30" viewBox="0 0 30 30"><circle cx="15" cy="9" r="5" fill="none" stroke="#fff" stroke-width="2.4"/><rect x="4" y="17" width="10" height="9" fill="#fff"/><rect x="16" y="17" width="10" height="9" fill="#fff"/></svg></div><h4>MANUFACTURING</h4><p>TQ Freight provides reliable, compliant, and efficient trucking solutions for the food and beverage industry.</p></div>
<div class="ind" style="left:243px;top:2360px"><div class="ico"><svg width="30" height="30" viewBox="0 0 30 30"><rect x="8" y="3" width="14" height="5" fill="#fff"/><rect x="7" y="9" width="16" height="18" rx="2" fill="none" stroke="#fff" stroke-width="2.4"/><path d="M15 13v9M10.5 17.5h9" stroke="#fff" stroke-width="2.4"/></svg></div><h4>PHARMA &amp; HEALTHCARE</h4><p>TQ Freight provides reliable, compliant, and efficient trucking solutions for the food and beverage industry.</p></div>
<div class="ind" style="left:594px;top:2360px"><div class="ico"><svg width="30" height="30" viewBox="0 0 30 30"><path d="M4 11 15 4l11 7z" fill="#fff"/><path d="M7 13v10M12 13v10M18 13v10M23 13v10" stroke="#fff" stroke-width="2.4"/><rect x="4" y="24" width="22" height="3" fill="#fff"/></svg></div><h4 style="top:40px">GOVERNMENT</h4><p style="top:78px">TQ Freight provides reliable, compliant, and efficient trucking solutions for the food and beverage industry.</p></div>

<!-- TESTIMONIALS -->
<div class="abs eyebrow" style="left:113px;top:2688px;color:var(--peach)">TESTIMONIALS</div>
<h2 class="abs display" style="left:112px;top:2712px;font-size:56px"><span class="accent">WHAT</span> <span style="color:var(--white)">PEOPLE SAYS</span></h2>

<div class="tcard" style="left:109px"><p>“Lorem ipsum dolor sit amet, consectetur adipiscing elit, sed do eiusmod tempor incididunt ut labore et dolore magna aliqua. Quis ipsum suspendisse ultrices gravida. Risus commodo viverra maece-nas accumsan lacus vel facilisis”</p><div class="who">Rhea Tolland</div><div class="stars">★★★★★</div><div class="src"></div></div>
<div class="tcard active" style="left:457px"><p>“Lorem ipsum dolor sit amet, consectetur adipiscing elit, sed do eiusmod tempor incididunt ut labore et dolore magna aliqua. Quis ipsum suspendisse ultrices gravida. Risus commodo viverra maece-nas accumsan lacus vel facilisis”</p><div class="who">Rhea Tolland</div><div class="stars">★★★★★</div><div class="src"></div></div>
<div class="tcard" style="left:806px"><p>“Lorem ipsum dolor sit amet, consectetur adipiscing elit, sed do eiusmod tempor incididunt ut labore et dolore magna aliqua. Quis ipsum suspendisse ultrices gravida. Risus commodo viverra maece-nas accumsan lacus vel facilisis”</p><div class="who">Rhea Tolland</div><div class="stars">★★★★★</div><div class="src"></div></div>

<svg class="abs" style="left:518px;top:3102px" width="176" height="32" viewBox="0 0 176 32">
  <circle cx="16" cy="16" r="15" fill="#3a1a10"/><path d="M22 16H10M15 11l-5 5 5 5" stroke="#fff" stroke-width="2" fill="none"/>
  <circle cx="52" cy="16" r="4" fill="#e8622e"/><circle cx="75" cy="16" r="4" fill="#e8d8ce"/><circle cx="98" cy="16" r="4" fill="#e8d8ce"/><circle cx="121" cy="16" r="4" fill="#e8d8ce"/>
  <circle cx="159" cy="16" r="15" fill="#e8622e"/><path d="M153 16h12M160 11l5 5-5 5" stroke="#fff" stroke-width="2" fill="none"/>
</svg>

<!-- CTA -->
<div class="abs" style="left:22px;top:3219px;width:1155px;height:543px;border-radius:6px;background:linear-gradient(90deg,#241009 0%,#5a2410 55%,#a0482a 100%)"></div>
<div class="photo" role="img" aria-label="White semi truck cab driving toward the viewer" style="left:22px;top:3219px;width:560px;height:543px;border-radius:6px 0 0 6px;background:linear-gradient(100deg,#3a2a24 0%,#b8aca6 45%,#e8e2de 60%,#5a3a2a 100%)"></div>
<div class="abs eyebrow" style="left:634px;top:3358px">CONTACT US</div>
<h2 class="abs display" style="left:633px;top:3387px;font-size:58px"><span class="accent">REQUEST</span> <span style="color:var(--white)">A QUOTE</span></h2>
<p class="abs" style="left:632px;top:3466px;width:480px;font-size:17px;line-height:1.45;color:var(--cream)">Lorem ipsum dolor sit amet, consectetur adipiscing elit, sed do eiusmod tempor incididunt ut labore et dolore magna aliqua. Quis ipsum suspendisse ultrices gravida.</p>
<div class="btn" style="left:634px;top:3563px">GET IN TOUCH<span class="arrow"><svg width="12" height="12" viewBox="0 0 12 12"><path d="M2 10 10 2M4 2h6v6" stroke="#fff" stroke-width="1.6" fill="none"/></svg></span></div>

<!-- FOOTER -->
<div class="abs" style="left:116px;top:3880px;display:flex;align-items:center;gap:10px"><div style="width:20px;height:20px;border-radius:50%;background:var(--orange)"></div><span style="font-family:'Oswald',sans-serif;font-weight:600;font-size:26px;color:var(--white)">TQ FREIGHT</span></div>
<div class="social" style="left:120px"></div>
<div class="social" style="left:167px"></div>
<div class="social" style="left:214px"></div>

<div class="abs" style="left:594px;top:3820px;width:1px;height:190px;background:var(--line)"></div>
<div class="abs" style="left:842px;top:3820px;width:1px;height:190px;background:var(--line)"></div>

<nav class="fnav">
  <a href="#"><svg width="14" height="14" viewBox="0 0 12 12"><path d="M6 1 1 6h2v5h2.5V8h1v3H9V6h2z" fill="#e8622e"/></svg>HOME</a>
  <a href="#"><svg width="14" height="14" viewBox="0 0 12 13"><circle cx="6" cy="4" r="3" fill="none" stroke="#e8622e" stroke-width="1.4"/><path d="M1 12c0-3 2.5-4.5 5-4.5s5 1.5 5 4.5" fill="none" stroke="#e8622e" stroke-width="1.4"/></svg>ABOUT</a>
  <a href="#"><svg width="14" height="14" viewBox="0 0 13 12"><path d="M1 11V4l3 2V4l3 2V1h2v10z" fill="#e8622e"/></svg>INDUSTRIES</a>
  <a href="#"><svg width="14" height="14" viewBox="0 0 13 13"><path d="M3 1l2 3-1.5 1.5c1 2 2 3 4 4L9 8l3 2-1.5 2.5C6 12 1 7 .8 2.5z" fill="#e8622e"/></svg>CONTACT US</a>
</nav>

<div class="fsvc">
  <h5><svg width="16" height="16" viewBox="0 0 13 13" style="margin-right:8px"><path d="M2 2l9 9M11 2 2 11" stroke="#e8622e" stroke-width="2"/></svg>SERVICES</h5>
  <ul style="margin-top:6px">
    <li>FLATBED</li><li>STEP DECK</li><li>DRY VAN</li><li>HEAVY HAUL</li>
  </ul>
</div>

<div class="fcontact">
  <h5>CONTACT US</h5>
  <div class="field" style="margin-top:18px"><svg width="10" height="10" viewBox="0 0 12 13"><circle cx="6" cy="4" r="3" fill="#c9b2a6"/><path d="M1 12c0-3 2.5-4.5 5-4.5s5 1.5 5 4.5z" fill="#c9b2a6"/></svg>Name</div>
  <div class="field"><svg width="11" height="9" viewBox="0 0 11 9"><rect width="11" height="9" fill="#c9b2a6"/><path d="M0 0l5.5 5L11 0" stroke="#1d0d09" fill="none"/></svg>Email address</div>
  <div class="field"><svg width="10" height="10" viewBox="0 0 13 13"><path d="M3 1l2 3-1.5 1.5c1 2 2 3 4 4L9 8l3 2-1.5 2.5C6 12 1 7 .8 2.5z" fill="#c9b2a6"/></svg>Phone</div>
  <div class="btn" style="position:relative;margin-top:14px;height:32px;width:112px;font-size:11px;padding-left:18px;gap:8px">SEND NOW<span class="arrow" style="width:24px;height:24px"><svg width="9" height="9" viewBox="0 0 12 12"><path d="M2 10 10 2M4 2h6v6" stroke="#fff" stroke-width="2" fill="none"/></svg></span></div>
</div>

<div class="abs" style="left:28px;top:4116px;width:1144px;height:1px;background:var(--line)"></div>
<p class="abs" style="left:0;width:1200px;top:4144px;text-align:center;font-size:13px;color:var(--cream)">© 2026. An independent agent of Halvern Partners LLC.</p>
<div class="abs" style="left:1059px;top:4135px;width:34px;height:34px;border-radius:50%;background:var(--orange);display:flex;align-items:center;justify-content:center"><svg width="16" height="14" viewBox="0 0 16 14"><path d="M2 1h12v9H6l-4 3z" fill="#fff"/></svg></div>
<div class="abs display" style="left:0;width:1200px;text-align:center;top:4168px;font-size:190px;color:#2a1712">TQ FREIGHT</div>

</div>
</body>
</html>
```